food delivery web site design

Currently we have a smartphone app (ios/android) that is being used by our clients to make orders to about 30 different restaurants.

We would like to extent this and have also a website that is able to mimic the same functionalities:
- register
- show restaurants based on the selected address
- make order to an restaurant
- being able to process orders for other registered users (please read the attached doc for complete info on this)

Take a look at the attached doc for more info.

```html
<!DOCTYPE html>
<html lang="ro">
<head>
<meta charset="utf-8">
<title>gustaMo – comandă mâncare</title>
<link rel="stylesheet" href="https://fonts.googleapis.com/css2?family=Bebas+Neue&family=Oswald:wght@400;500&family=Open+Sans:wght@400&display=swap">
<style>
  :root {
    --red: #9c150a;
    --red-dark: #7e0f06;
    --gold: #f2c94c;
    --yellow: #f5dc6a;
    --white: #ffffff;
    --ink: #1c1c1c;
    --footer: #1b1b1b;
    --footer-text: #e8e8e8;
    --field-text: #6c6c6c;
  }
  * { box-sizing: border-box; margin: 0; padding: 0; }
  html, body { width: 1200px; height: 666px; overflow: hidden; }
  body { position: relative; font-family: "Open Sans", sans-serif; background: #efe3dc; }

  .hero-photo {
    position: absolute; left: 0; top: 0; width: 1200px; height: 611px;
    background:
      radial-gradient(ellipse 260px 120px at 820px 240px, #f5ecc2 0%, rgba(245,236,194,0) 100%),
      radial-gradient(ellipse 300px 140px at 360px 250px, #f8eee0 0%, rgba(248,238,224,0) 100%),
      radial-gradient(ellipse 200px 120px at 90px 330px, #e4d3d0 0%, rgba(228,211,208,0) 100%),
      linear-gradient(180deg, #d8cbc8 0%, #eee4df 45%, #f1e6d6 75%, #e8dccf 100%);
  }

  .topbar {
    position: absolute; left: 0; top: 51px; width: 1200px; height: 52px;
    background: var(--red);
    border-top: 2px solid var(--red-dark); border-bottom: 2px solid var(--red-dark);
  }
  .topbar::before, .topbar::after {
    content: ""; position: absolute; left: 0; right: 0; height: 1px; background: rgba(255,255,255,.35);
  }
  .topbar::before { top: 3px; }
  .topbar::after { bottom: 3px; }

  .rule { position: absolute; height: 3px; border-top: 1px solid rgba(255,255,255,.6); border-bottom: 1px solid rgba(255,255,255,.6); top: 77px; }
  .rule-dotted { position: absolute; top: 77px; left: 609px; width: 277px; border-top: 2px dotted rgba(255,255,255,.55); }

  .brand-badge { position: absolute; left: 140px; top: 0; width: 156px; height: 158px; }
  .brand-name {
    position: absolute; left: 163px; top: 64px; width: 110px; text-align: center;
    font-family: "Bebas Neue", sans-serif; font-size: 28px; color: var(--red); letter-spacing: .5px;
  }

  .call {
    position: absolute; left: 350px; top: 62px;
    font-family: "Bebas Neue", sans-serif; font-size: 29px; color: var(--white); letter-spacing: .3px;
    display: flex; align-items: center; gap: 6px;
  }
  .call .phone { color: var(--gold); display: flex; align-items: center; gap: 3px; }

  .account { position: absolute; top: 66px; font-family: "Bebas Neue", sans-serif; font-size: 19px; color: var(--white); display: flex; align-items: center; gap: 6px; }
  .account.login { left: 905px; }
  .account.signup { left: 980px; }

  .headline { position: absolute; left: 138px; top: 206px; font-family: "Bebas Neue", sans-serif; font-size: 40px; color: var(--ink); }
  .tagline { position: absolute; left: 138px; top: 258px; font-size: 19.5px; color: var(--ink); }

  .search-panel {
    position: absolute; left: 138px; top: 310px; width: 924px; height: 261px;
    background: var(--red); border-bottom: 4px solid var(--yellow);
  }
  .search-panel::before {
    content: ""; position: absolute; inset: 4px; border: 1px solid rgba(255,255,255,.45);
  }
  .label { position: absolute; font-family: "Oswald", sans-serif; font-weight: 500; font-size: 15px; color: var(--white); letter-spacing: .4px; }
  .field {
    position: absolute; top: 46px; height: 51px; background: var(--white);
    font-family: "Oswald", sans-serif; font-size: 19px; color: var(--field-text);
    display: flex; align-items: center; padding-left: 12px; white-space: nowrap; overflow: hidden;
  }
  .field.address { left: 28px; width: 534px; }
  .field.city { left: 581px; width: 196px; justify-content: space-between; padding-right: 14px; }
  .show-btn {
    position: absolute; left: 795px; top: 46px; width: 102px; height: 51px; background: var(--yellow);
    font-family: "Oswald", sans-serif; font-weight: 500; font-size: 14.5px; line-height: 19px; color: var(--red);
    display: flex; align-items: center; justify-content: center; text-align: center;
  }
  .reco-label { position: absolute; left: 28px; top: 118px; font-family: "Oswald", sans-serif; font-size: 13.5px; color: var(--white); }
  .reco-rule { position: absolute; left: 195px; top: 127px; width: 702px; height: 3px; border-top: 1px solid rgba(255,255,255,.6); border-bottom: 1px solid rgba(255,255,255,.6); }

  .restaurant { position: absolute; top: 149px; width: 270px; height: 100px; }
  .restaurant .thumb { position: absolute; left: 0; top: 0; width: 92px; height: 74px; }
  .restaurant .stars { position: absolute; left: 0; top: 80px; font-size: 12px; color: var(--gold); letter-spacing: 2px; }
  .restaurant .name { position: absolute; left: 102px; top: -4px; font-family: "Oswald", sans-serif; font-size: 20px; color: var(--white); white-space: nowrap; }
  .restaurant .facts { position: absolute; left: 102px; top: 28px; list-style: none; }
  .restaurant .facts li {
    height: 22px; display: flex; align-items: center; gap: 10px;
    font-family: "Oswald", sans-serif; font-size: 12.5px; color: var(--white);
  }
  .restaurant .facts svg { width: 13px; height: 13px; }

  .site-footer {
    position: absolute; left: 0; top: 611px; width: 1200px; height: 55px; background: var(--footer);
    border-top: 3px solid #d9d0cb;
  }
  .footer-links { position: absolute; left: 138px; top: 16px; display: flex; font-size: 12.5px; color: var(--footer-text); list-style: none; }
  .footer-links li + li::before { content: "|"; color: #666; margin: 0 9px; }
  .copyright { position: absolute; right: 138px; top: 16px; font-size: 12.5px; color: var(--footer-text); }
</style>
</head>
<body>

<div class="hero-photo" role="img" aria-label="Fotografie de fundal cu deserturi pe o farfurie albă, estompată"></div>

<header>
  <div class="topbar"></div>
  <div class="rule" style="left:296px;width:36px"></div>
  <div class="rule-dotted"></div>
  <div class="rule" style="left:1063px;width:137px"></div>

  <svg class="brand-badge" viewBox="0 0 156 158" aria-hidden="true">
    <path d="M0 0 H156 V130 L128 158 H28 L0 130 Z" fill="#9c150a"/>
    <path d="M5 0 V127 L30 152 H126 L151 127 V0" fill="none" stroke="rgba(255,255,255,.45)" stroke-width="1"/>
    <circle cx="78" cy="78" r="56" fill="#ffffff"/>
  </svg>
  <div class="brand-name">gustaMo</div>

  <div class="call">SUNĂ-NE LA
    <span class="phone">
      <svg width="16" height="18" viewBox="0 0 16 18" aria-hidden="true"><path d="M3 1 L6 1 L7 5 L5 7 C6 10 8 12 10 13 L12 11 L15 12 L15 15 C15 16 14 17 13 17 C6 16 1 10 1 3 C1 2 2 1 3 1 Z" fill="#f2c94c"/></svg>
      0700 123 456
    </span>
  </div>

  <div class="account login">
    <svg width="14" height="13" viewBox="0 0 14 13" aria-hidden="true"><path d="M1 12 V7 C1 5 2 4 4 4 H9 V1 L14 5.5 L9 10 V7 H4 V12 Z" fill="#fff"/></svg>
    LOGIN
  </div>
  <div class="account signup">
    <svg width="15" height="13" viewBox="0 0 15 13" aria-hidden="true"><circle cx="6" cy="4" r="3" fill="#fff"/><path d="M0 12 C0 8 3 7.5 6 7.5 C9 7.5 12 8 12 12 Z" fill="#fff"/><path d="M12 2 V6 M10 4 H14" stroke="#fff" stroke-width="1.6"/></svg>
    SIGN IN
  </div>
</header>

<main>
  <h1 class="headline">ȚI-E FOAME ?</h1>
  <p class="tagline">Comandă direct de pe mobil mancărurile favorite de la restaurantul tău preferat.</p>

  <section class="search-panel">
    <span class="label" style="left:28px;top:19px">INTRODU ADRESA</span>
    <span class="label" style="left:581px;top:19px">ALEGE ORAȘUL</span>
    <div class="field address">LOREM IPSUM DOLOR SIT AMET, CONSECTETUER ADIPISCING ELIT. AENEAN COMMODO</div>
    <div class="field city">BUCUREȘTI
      <svg width="12" height="9" viewBox="0 0 12 9" aria-hidden="true"><path d="M0 0 H12 L6 9 Z" fill="#6c6c6c"/></svg>
    </div>
    <div class="show-btn">AFIȘEAZĂ<br>RESTAURANTE</div>

    <span class="reco-label">RESTAURANTE RECOMANDATE</span>
    <div class="reco-rule"></div>

    <article class="restaurant" style="left:28px">
      <div class="thumb" role="img" aria-label="Imagine restaurant" style="background:linear-gradient(135deg,#8a7a68,#4a3e34)"></div>
      <div class="stars">★★★★★</div>
      <h2 class="name">La Oala Veche</h2>
      <ul class="facts">
        <li><svg viewBox="0 0 13 13"><path d="M5.5 0 H7.5 V13 H5.5 Z M1 2 H11 L12.5 3.5 L11 5 H1 Z M2 7 H12 V10 H2 L0.5 8.5 Z" fill="#f2c94c"/></svg>3KM</li>
        <li><svg viewBox="0 0 13 13"><ellipse cx="5" cy="4" rx="5" ry="2" fill="#f2c94c"/><ellipse cx="5" cy="7" rx="5" ry="2" fill="#f2c94c"/><ellipse cx="8" cy="10" rx="5" ry="2" fill="#f2c94c"/></svg>25RON</li>
        <li><svg viewBox="0 0 13 13"><path d="M1 1 L12 12 M4 1 L12 9" stroke="#f2c94c" stroke-width="1.6"/></svg>ROMANESC</li>
      </ul>
    </article>

    <article class="restaurant" style="left:323px">
      <div class="thumb" role="img" aria-label="Imagine restaurant" style="background:linear-gradient(180deg,#ffffff,#eef2ec)"></div>
      <div class="stars">★★★★★</div>
      <h2 class="name">Grădina Verde</h2>
      <ul class="facts">
        <li><svg viewBox="0 0 13 13"><path d="M5.5 0 H7.5 V13 H5.5 Z M1 2 H11 L12.5 3.5 L11 5 H1 Z M2 7 H12 V10 H2 L0.5 8.5 Z" fill="#f2c94c"/></svg>12KM</li>
        <li><svg viewBox="0 0 13 13"><ellipse cx="5" cy="4" rx="5" ry="2" fill="#f2c94c"/><ellipse cx="5" cy="7" rx="5" ry="2" fill="#f2c94c"/><ellipse cx="8" cy="10" rx="5" ry="2" fill="#f2c94c"/></svg>50RON</li>
        <li><svg viewBox="0 0 13 13"><path d="M1 1 L12 12 M4 1 L12 9" stroke="#f2c94c" stroke-width="1.6"/></svg>ITALIAN</li>
      </ul>
    </article>

    <article class="restaurant" style="left:591px">
      <div class="thumb" role="img" aria-label="Imagine restaurant" style="background:linear-gradient(180deg,#ffffff,#f2f2f2)"></div>
      <div class="stars">★★★★☆</div>
      <h2 class="name">Atelier Nord</h2>
      <ul class="facts">
        <li><svg viewBox="0 0 13 13"><path d="M5.5 0 H7.5 V13 H5.5 Z M1 2 H11 L12.5 3.5 L11 5 H1 Z M2 7 H12 V10 H2 L0.5 8.5 Z" fill="#f2c94c"/></svg>14KM</li>
        <li><svg viewBox="0 0 13 13"><ellipse cx="5" cy="4" rx="5" ry="2" fill="#f2c94c"/><ellipse cx="5" cy="7" rx="5" ry="2" fill="#f2c94c"/><ellipse cx="8" cy="10" rx="5" ry="2" fill="#f2c94c"/></svg>75RON</li>
        <li><svg viewBox="0 0 13 13"><path d="M1 1 L12 12 M4 1 L12 9" stroke="#f2c94c" stroke-width="1.6"/></svg>CONTEMPORAN, INTERNATIONAL</li>
      </ul>
    </article>
  </section>
</main>

<footer class="site-footer">
  <ul class="footer-links">
    <li>Contactează-ne</li>
    <li>Despre noi</li>
    <li>Partenerii noștri</li>
    <li>FAQ</li>
    <li>Devino partener</li>
  </ul>
  <p class="copyright">Copyright © 2013 gustaMo.ro. Toate drepturile rezervate.</p>
</footer>

</body>
</html>
```